OrvanoGoodsHub.com -Ecommerce Website for Luxury Products

This will be an ecommerce site. A website portal that will allow both consumers to enter one way and see specific purchase options and businesses to enter via a different link that allows B2B to see their specific options once logged into. B2C can purchase both as a guest/or after account is setup. B2B must be approved to set up account. This is front end website project. Back-end integration is separate. Will be hosted on Servantia with a domain registration held at Pexadrinet. Additional website concept/idea/synergy can be found from sister site-KRWZHospitality.com

```html
<!DOCTYPE html>
<html lang="en">
<head>
<meta charset="utf-8">
<title>OrvanoGoods — Luxury Lifestyle Accoutrements</title>
<link href="https://fonts.googleapis.com/css2?family=Playfair+Display:ital,wght@0,400;0,600;1,400&family=Poppins:wght@400;500&display=swap" rel="stylesheet">
<style>
:root{
  --gold:#f5a623;
  --gold-deep:#e0901a;
  --ink:#1b1510;
  --dark:#1c140d;
  --dark-2:#2a1d12;
  --cream:#fdf5e7;
  --cream-2:#fbeed8;
  --white:#ffffff;
  --muted:#5a4a3a;
}
*{box-sizing:border-box;margin:0;padding:0}
html,body{width:1200px;height:3364px;overflow:hidden}
body{position:relative;font-family:"Poppins",sans-serif;color:var(--ink);background:var(--white)}
.abs{position:absolute}
.serif{font-family:"Playfair Display",serif}
.btn{position:absolute;display:flex;align-items:center;gap:12px;background:var(--gold);color:var(--ink);font-size:15px;font-weight:500;padding:0 22px;height:44px;border-radius:3px}
.btn svg{width:22px;height:12px}
.crown{position:absolute;width:46px;height:26px}
.eyebrow{position:absolute;font-size:18px;letter-spacing:3px;text-transform:uppercase}
.photo{position:absolute;border-radius:999px 999px 0 0}

/* hero */
.hero{position:absolute;left:0;top:0;width:1200px;height:600px;background:linear-gradient(180deg,#fff 0%,#fff 60%,var(--cream-2) 100%)}
.brand{position:absolute;text-align:center}
.brand-name{font-family:"Playfair Display",serif;font-weight:600;letter-spacing:2px;color:var(--ink)}
.brand-sub{font-family:"Playfair Display",serif;font-size:11px;letter-spacing:2px;color:var(--ink)}
.nav{position:absolute;left:380px;top:58px;display:flex;gap:26px;font-size:15px}
.nav .active{color:var(--gold);border-bottom:2px solid var(--gold);padding-bottom:4px}
.hero h1{position:absolute;left:112px;top:218px;font-family:"Playfair Display",serif;font-weight:600;font-size:44px;line-height:1.2}
.hero h1 span{color:var(--gold)}
.hero .tag{position:absolute;left:112px;top:336px;font-family:"Playfair Display",serif;font-style:italic;font-size:30px}
.hero .lede{position:absolute;left:112px;top:392px;font-size:15px}

/* featured */
.featured{position:absolute;left:0;top:600px;width:1200px;height:900px;background:linear-gradient(180deg,#3a2816 0%,var(--dark) 30%,#0f0a06 100%);color:var(--white)}
.featured .title{position:absolute;width:1200px;text-align:center;top:140px;font-size:44px;font-weight:600}
.featured .intro{position:absolute;width:1200px;text-align:center;top:234px;font-size:16px}
.card-cap{position:absolute;width:300px;text-align:center;font-family:"Playfair Display",serif;font-style:italic;font-size:26px}
.arrow-side{position:absolute;top:460px;width:20px;height:36px}

/* about */
.about{position:absolute;left:0;top:1500px;width:1200px;height:600px;background:linear-gradient(180deg,var(--cream) 0%,#fff 100%)}
.heading-gold{position:absolute;font-family:"Playfair Display",serif;font-weight:600;font-size:40px;color:var(--gold)}
.body-text{position:absolute;font-size:15px;line-height:1.6;color:var(--ink)}

/* partners */
.partners{position:absolute;left:0;top:2100px;width:1200px;height:330px;background:#fff}
.badge{position:absolute;top:2316px;height:28px;border-radius:14px;background:#3c3c4a}

/* contact */
.contact{position:absolute;left:0;top:2430px;width:1200px;height:440px;background:linear-gradient(180deg,#4a3219 0%,#24180e 45%,#120c07 100%);color:var(--white);text-align:center}

/* footer */
.footer{position:absolute;left:0;top:2870px;width:1200px;height:494px;background:linear-gradient(180deg,#fff 0%,var(--cream) 100%)}
.fnav{position:absolute;left:0;width:1200px;top:3172px;display:flex;justify-content:center;gap:28px;font-size:15px}
.fnav .active{color:var(--gold)}
.social{width:22px;height:22px;border-radius:50%;background:var(--ink)}
</style>
</head>
<body>

<!-- HERO -->
<section class="hero">
  <div class="brand" style="left:100px;top:36px;width:250px">
    <div style="width:40px;height:40px;margin:0 auto 8px;border:2px solid var(--ink)"></div>
    <div class="brand-name" style="font-size:28px">ORVANOGOODS</div>
    <div class="brand-sub">A DIVISION OF KRWZ HOSPITALITY</div>
  </div>
  <nav class="nav">
    <span class="active">Home</span><span>About</span><span>Retail Collection</span><span>Wholesale Portal</span><span>Partners</span><span>Contact and Concierge</span>
  </nav>
  <h1>Curated for Connoisseurs,<br><span>Crafted for Lounges.</span></h1>
  <div class="tag">Elevate Your Lounge. Impress Your Clientele.</div>
  <p class="lede">From the humidor to the wardrobe - OrvanoGoods delivers indulgence.</p>
  <div class="btn" style="left:112px;top:452px">Shop Now <svg viewBox="0 0 22 12"><path d="M0 6h19M14 1l6 5-6 5" stroke="#1b1510" stroke-width="2" fill="none"/></svg></div>
  <div class="photo" role="img" aria-label="Busy upscale lounge bar with guests and warm lighting" style="left:772px;top:120px;width:316px;height:460px;background:linear-gradient(180deg,#6b5236 0%,#3a2a1c 55%,#1e150e 100%)"></div>
</section>

<!-- FEATURED -->
<section class="featured">
  <svg class="crown" style="left:577px;top:44px" viewBox="0 0 46 26"><path d="M3 22L6 6l10 9 7-13 7 13 10-9 3 16z" fill="#f5a623"/></svg>
  <div class="eyebrow" style="width:1200px;text-align:center;top:80px;color:var(--gold)">Our Retail Products</div>
  <h2 class="title serif">Featured Collections</h2>
  <p class="intro">Signature pieces curated for the modern connoisseur, from the cigar lounge to the private wardrobe.</p>
  <svg class="arrow-side" style="left:36px" viewBox="0 0 20 36"><path d="M18 2L3 18l15 16" stroke="#f5a623" stroke-width="3" fill="none"/></svg>
  <svg class="arrow-side" style="left:1144px" viewBox="0 0 20 36"><path d="M2 2l15 16L2 34" stroke="#f5a623" stroke-width="3" fill="none"/></svg>
  <div class="photo" role="img" aria-label="Cigar cutter and accessories on leather" style="left:120px;top:312px;width:300px;height:360px;background:linear-gradient(160deg,#6a4a2e,#2b1d12)"></div>
  <div class="photo" role="img" aria-label="Fragrance and oil bottles on a shelf" style="left:448px;top:312px;width:304px;height:360px;background:linear-gradient(160deg,#b08a44,#4a3418)"></div>
  <div class="photo" role="img" aria-label="Leather boots and tailored attire" style="left:780px;top:312px;width:300px;height:360px;background:linear-gradient(160deg,#5a4430,#1e150e)"></div>
  <div class="btn" style="left:500px;top:612px;height:40px;font-size:14px">Browse Collection <svg viewBox="0 0 22 12"><path d="M0 6h19M14 1l6 5-6 5" stroke="#1b1510" stroke-width="2" fill="none"/></svg></div>
  <div class="card-cap" style="left:120px;top:696px">Cigar Accessories</div>
  <div class="card-cap" style="left:450px;top:696px;color:var(--gold)">Oils &amp; Fragrances</div>
  <div class="card-cap" style="left:780px;top:696px">Attire &amp; Accessories</div>
  <p class="abs" style="left:470px;top:752px;width:260px;text-align:center;font-size:15px;line-height:1.5">An olfactory wardrobe designed for both the individual and the room.</p>
</section>

<!-- ABOUT -->
<section class="about">
  <div class="photo" role="img" aria-label="Person seated at a dimly lit lounge bar" style="left:112px;top:92px;width:310px;height:450px;background:linear-gradient(180deg,#7a5c3c 0%,#3a2818 60%,#1c130b 100%)"></div>
  <svg class="crown" style="left:540px;top:110px" viewBox="0 0 46 26"><path d="M3 22L6 6l10 9 7-13 7 13 10-9 3 16z" fill="#f5a623"/></svg>
  <div class="eyebrow" style="left:540px;top:146px">Who We Are</div>
  <div class="heading-gold" style="left:540px;top:180px">Purveyors of the Luxe Lifestyle</div>
  <p class="body-text" style="left:540px;top:252px;width:530px">OrvanoGoods is a division of KRWZ Hospitality, created to serve as the quiet curator behind the most memorable luxury experiences. Rooted in lounge culture and refined hospitality, OrvanoGoods brings together artisans, makers, and designers under one considered brand. Our mission is to source and develop limited-edition and one-of-a-kind lifestyle accoutrements that honor tradition while speaking fluently to today's luxury consumer.</p>
  <div class="btn" style="left:540px;top:450px;height:40px;font-size:14px">Learn More <svg viewBox="0 0 22 12"><path d="M0 6h19M14 1l6 5-6 5" stroke="#1b1510" stroke-width="2" fill="none"/></svg></div>
</section>

<!-- PARTNERS -->
<section class="partners">
  <svg class="crown" style="left:112px;top:22px" viewBox="0 0 46 26"><path d="M3 22L6 6l10 9 7-13 7 13 10-9 3 16z" fill="#f5a623"/></svg>
  <div class="eyebrow" style="left:112px;top:58px">Our Partners</div>
  <div class="heading-gold" style="left:112px;top:92px">Proud Partners</div>
  <p class="body-text" style="left:540px;top:42px;width:548px">OrvanoGoods is proud to collaborate with a select circle of lounges and hospitality venues that share a commitment to elevated experience. The Partner Showcase highlights spaces where guests can encounter OrvanoGoods collections in their natural habitat.</p>
</section>
<div class="badge" role="img" aria-label="Partner badge" style="left:112px;width:120px"></div>
<div class="badge" role="img" aria-label="Partner badge" style="left:310px;width:150px"></div>
<div class="badge" role="img" aria-label="Partner badge" style="left:530px;width:130px"></div>
<div class="badge" role="img" aria-label="Partner badge" style="left:725px;width:140px"></div>
<div class="badge" role="img" aria-label="Partner badge" style="left:945px;width:130px"></div>

<!-- CONTACT -->
<section class="contact">
  <svg class="crown" style="left:577px;top:82px" viewBox="0 0 46 26"><path d="M3 22L6 6l10 9 7-13 7 13 10-9 3 16z" fill="#f5a623"/></svg>
  <div class="eyebrow" style="width:1200px;top:118px;color:var(--gold)">Get In Touch</div>
  <h2 class="abs serif" style="width:1200px;top:150px;font-size:44px;font-weight:600">Contact &amp; Concierge</h2>
  <p class="abs" style="left:340px;width:520px;top:234px;font-size:15px;line-height:1.6">For personal purchases, custom commissions, and B2B collaborations, the OrvanoGoods Concierge team is at your service.</p>
  <div class="btn" style="left:516px;top:318px;height:40px;font-size:14px">Contact Us <svg viewBox="0 0 22 12"><path d="M0 6h19M14 1l6 5-6 5" stroke="#1b1510" stroke-width="2" fill="none"/></svg></div>
</section>

<!-- FOOTER -->
<footer class="footer">
  <div class="abs" role="img" aria-label="Fountain pen and keys on a surface" style="left:0;top:60px;width:260px;height:170px;background:radial-gradient(ellipse at 40% 50%,#5b4330 0%,rgba(91,67,48,0) 70%)"></div>
  <div class="abs" role="img" aria-label="Rose petals and a perfume bottle" style="left:930px;top:0;width:270px;height:230px;background:radial-gradient(ellipse at 60% 50%,#e9b8ad 0%,rgba(233,184,173,0) 70%)"></div>
  <div class="brand" style="left:400px;top:40px;width:400px">
    <div style="width:54px;height:54px;margin:0 auto 10px;border:2px solid var(--ink)"></div>
    <div class="brand-name" style="font-size:44px">ORVANOGOODS</div>
    <div class="brand-sub" style="font-size:13px;margin-top:4px">A DIVISION OF KRWZ HOSPITALITY</div>
    <div class="serif" style="font-size:20px;margin-top:22px">Purveyors of Luxury Lifestyle Accoutrements</div>
  </div>
</footer>
<nav class="fnav"><span class="active">Home</span><span>About</span><span>Retail Collection</span><span>Wholesale Portal</span><span>Partners</span><span>Contact and Concierge</span></nav>
<div class="abs" style="left:250px;top:3228px;width:220px;height:40px;border:1px solid #c9b9a4;background:#fff;font-size:13px;color:#8a7a68;padding:11px 14px">Email Address</div>
<div class="btn" style="left:470px;top:3228px;height:40px;font-size:14px">Get Updates <svg viewBox="0 0 22 12"><path d="M0 6h19M14 1l6 5-6 5" stroke="#1b1510" stroke-width="2" fill="none"/></svg></div>
<div class="abs" style="left:680px;top:3238px;display:flex;align-items:center;gap:12px;font-size:15px">Follow Us <span class="social"></span><span class="social"></span><span class="social"></span><span class="social"></span><span class="social"></span></div>
<p class="abs" style="width:1200px;text-align:center;top:3312px;font-size:12px;color:var(--muted)">Copyright © 2025 OrvanoGoods. All Rights Reserved.</p>

</body>
</html>
```